Folded A4 flyer for design&construction company

Folded A4 flyer needed. Keywords: elegant, stylish
our website www.dorvika.ae

Industry/Entity Type

Construction

```html
<!DOCTYPE html>
<html lang="en">
<head>
<meta charset="utf-8">
<title>Dorvika – Folded Flyer</title>
<link href="https://fonts.googleapis.com/css2?family=Open+Sans:ital,wght@0,300;0,400;0,600;0,700;1,700&family=Lobster+Two:ital,wght@1,400;1,700&display=swap" rel="stylesheet">
<style>
  :root{
    --page:#ececec;
    --slate:#555557;
    --gold:#c39a2f;
    --gold-light:#e6c35a;
    --gold-deep:#a67d1c;
    --white:#ffffff;
    --ink:#3a3a3a;
    --orange:#f7a823;
  }
  *{box-sizing:border-box;margin:0;padding:0}
  html,body{width:777px;height:1200px;overflow:hidden}
  body{background:var(--page);font-family:"Open Sans",Arial,sans-serif;position:relative;color:var(--white)}
  .panel{position:absolute;left:75px;width:631px;height:446px;background:var(--slate);overflow:hidden}
  .panel--outer{top:113px}
  .panel--inner{top:636px}
  .abs{position:absolute}

  /* outer spread */
  .brand-small{left:67px;top:58px;width:181px;text-align:center;font-size:24px;font-weight:400;letter-spacing:1px;line-height:1}
  .intro{left:45px;top:103px;width:226px;font-size:8.2px;line-height:10.8px;text-align:justify}
  .ornament{border-radius:50%;background:radial-gradient(ellipse at center,#8e8e90 0%,#6a6a6c 55%,rgba(85,85,87,0) 72%)}
  .ornament--grey{left:59px;top:199px;width:195px;height:80px}
  .quote-badge{left:38px;top:271px;width:72px;height:72px;border-radius:50%;background:radial-gradient(circle,#ffd04a 0%,var(--orange) 70%,#e88f12 100%);display:flex;align-items:center;justify-content:center;text-align:center;color:#5a3b0a;transform:rotate(-18deg)}
  .quote-badge span{display:block;font-weight:700;line-height:1}
  .quote-badge .small{font-size:7px}
  .quote-badge .big{font-size:13px}
  .phone{left:122px;top:300px;font-size:13px}
  .or-pill{left:147px;top:322px;width:24px;height:14px;border-radius:7px;background:var(--gold);font-size:10px;line-height:14px;text-align:center}
  .email{left:106px;top:340px;font-size:10.5px}
  .web-bar{height:18px;background:linear-gradient(90deg,rgba(195,154,47,0) 0%,var(--gold-deep) 12%,var(--gold-light) 50%,var(--gold-deep) 88%,rgba(195,154,47,0) 100%);text-align:center;font-size:10px;font-weight:700;line-height:18px;letter-spacing:.3px}
  .web-bar--left{left:37px;top:387px;width:234px}
  .web-bar--right{left:347px;top:411px;width:248px}
  .address{left:0;width:315px;top:419px;text-align:center;font-size:7.6px}
  .brand-large{left:343px;top:78px;width:264px;text-align:center;font-size:40px;font-weight:300;letter-spacing:1px;line-height:1}
  .tagline{left:363px;top:124px;width:224px;text-align:center;font-size:11px;color:var(--gold)}
  .photo-hero{left:316px;top:151px;width:315px;height:226px;background:linear-gradient(135deg,#f4f1ea 0%,#f0b43a 35%,#e9a022 55%,#c98d45 80%,#f3efe6 100%)}
  .quote{left:316px;width:315px;top:353px;text-align:center;font-family:"Lobster Two",cursive;font-style:italic;font-weight:400;font-size:12px;text-shadow:0 1px 2px rgba(0,0,0,.35)}

  /* inner spread */
  .band{left:0;top:0;width:631px;height:48px;background:var(--gold);border-bottom:2px solid var(--white)}
  .band-text{top:15px;font-size:14px;font-weight:700;font-style:italic}
  .band-text--left{left:39px}
  .band-text--right{left:391px}
  .seal{left:259px;top:-12px;width:116px;height:116px;border-radius:50%;background:var(--white);border:3px solid var(--gold);display:flex;flex-direction:column;align-items:center;justify-content:center;color:var(--ink)}
  .seal .name{font-size:21px;font-weight:400;line-height:1;padding-top:14px}
  .seal .sub{font-size:6.5px;color:var(--gold);margin-top:2px}
  .service{top:84px;width:140px}
  .service h2{font-size:20px;font-weight:400;line-height:1;text-align:center;letter-spacing:.3px}
  .service h3{font-size:11px;font-weight:700;color:var(--gold);text-align:center;margin-top:2px}
  .service ul{list-style:none;margin-top:12px}
  .service li{font-size:8.4px;line-height:10.8px;padding-left:7px;position:relative;white-space:nowrap}
  .service li::before{content:"";position:absolute;left:0;top:4px;width:3px;height:3px;border-radius:50%;background:var(--white)}
  .service--design{left:9px}
  .service--design ul{margin-left:29px}
  .service--landscaping{left:151px}
  .service--landscaping ul{margin-left:26px}
  .service--fitout{left:343px}
  .service--fitout ul{margin-left:27px}
  .service--maintenance{left:483px}
  .service--maintenance ul{margin-left:28px}
  .divider{left:315px;top:120px;width:1px;height:104px;background:var(--gold)}
  .gallery{top:244px;height:202px}
  .gallery--lounge{left:10px;width:191px;background:linear-gradient(160deg,#d9cbb0 0%,#5b4a3a 40%,#8a5a2c 70%,#b77838 100%)}
  .gallery--terrace{left:206px;width:200px;background:linear-gradient(180deg,#f2f2f2 0%,#d8d9db 50%,#8d8a86 100%)}
  .gallery--living{left:411px;width:211px;background:linear-gradient(150deg,#efe0c6 0%,#b9906a 45%,#8e5e38 75%,#d9c2a3 100%)}
  .arch{left:0;top:244px}
  .ornament--gold{left:191px;top:384px;width:256px;height:56px;border-radius:50%;background:radial-gradient(ellipse at center,var(--gold-light) 0%,var(--gold) 45%,rgba(195,154,47,0) 72%)}
</style>
</head>
<body>

<section class="panel panel--outer">
  <div class="abs brand-small">DORVIKA</div>
  <p class="abs intro">We believe in quality beginnings and flawless finishes. We are a team of creative designers and constructors with years of experience and expertise in providing complete interior design and construction services. Our unique designing prowess is complemented by our unflinching commitment to quality construction. Our team specializes in classic and contemporary high quality construction in Dubai for commercial and residential projects.</p>
  <div class="abs ornament ornament--grey" role="img" aria-label="Grey scrollwork flourish ornament"></div>

  <div class="abs quote-badge"><div><span class="small">GET A</span><span class="big">FREE</span><span class="big">QUOTE</span><span class="small">TODAY</span></div></div>
  <div class="abs phone">800-DORVIKA</div>
  <div class="abs or-pill">or</div>
  <div class="abs email">CONTACT@DORVIKA.AE</div>
  <div class="abs web-bar web-bar--left">WWW.DORVIKA.AE</div>
  <div class="abs address">Dorvika LLC, Palm Crest Tower, Suite 708, Marina Quarter, Dubai</div>

  <div class="abs brand-large">DORVIKA</div>
  <div class="abs tagline">design &amp; construction</div>
  <div class="abs photo-hero" role="img" aria-label="Modern interior with curved orange ceiling, white staircase and wooden floor"></div>
  <div class="abs quote">Quality is not an act, it is a habit - Anonymous</div>
  <div class="abs web-bar web-bar--right">WWW.DORVIKA.AE</div>
</section>

<section class="panel panel--inner">
  <div class="abs band"></div>
  <div class="abs band-text band-text--left">Customized Design Solutions...</div>
  <div class="abs band-text band-text--right">From Concept to Completion</div>
  <div class="abs seal"><span class="name">DORVIKA</span><span class="sub">design &amp; construction</span></div>

  <div class="abs service service--design">
    <h2>DORVIKA</h2><h3>design</h3>
    <ul><li>Villas Interior Design</li><li>Villas Exterior Design</li><li>Landscape Design</li><li>Retail Interior Design</li><li>Office Interior Design</li><li>Hospitality Interior Design</li><li>Hotel Interior Design</li><li>Hotel Exterior Design</li><li>Restaurant Interior Design</li></ul>
  </div>
  <div class="abs service service--landscaping">
    <h2>DORVIKA</h2><h3>landscaping</h3>
    <ul><li>Soft Landscaping</li><li>Irrigation Solutions</li><li>Hard Landscaping</li><li>External Lighting</li><li>Swimming Pool<br>&amp; Water Features</li></ul>
  </div>
  <div class="abs divider"></div>
  <div class="abs service service--fitout">
    <h2>DORVIKA</h2><h3>fitout</h3>
    <ul><li>Development Approvals</li><li>Flooring Solutions</li><li>Partition</li><li>Sealing Solutions</li><li>MEP Works</li><li>Civil Works</li><li>Joinery</li><li>Glass and Aluminum Works<br>(Subcontractor)</li></ul>
  </div>
  <div class="abs service service--maintenance">
    <h2>DORVIKA</h2><h3>maintenance</h3>
    <ul><li>AC Repair</li><li>Plumber Services</li><li>Electric Repair</li><li>Carpentry Work</li><li>Gypsum Ceiling</li><li>Painting Services</li><li>Cleaning Services</li><li>Emergency Services</li></ul>
  </div>

  <div class="abs gallery gallery--lounge" role="img" aria-label="Classic lounge with stone fireplace wall and wooden floor"></div>
  <div class="abs gallery gallery--terrace" role="img" aria-label="Bright rooftop terrace with white sofas"></div>
  <div class="abs gallery gallery--living" role="img" aria-label="Elegant living room with arches, chandelier and armchairs"></div>
  <svg class="abs arch" width="631" height="202" viewBox="0 0 631 202" aria-hidden="true">
    <path d="M112 202 C140 140 230 104 317 104 C404 104 494 140 522 202 Z" fill="var(--slate)"/>
    <rect x="189" y="188" width="256" height="2" fill="var(--gold)"/>
  </svg>
  <div class="abs ornament--gold" role="img" aria-label="Gold scrollwork flourish ornament"></div>
</section>

</body>
</html>
```